Business Card for Fashion House

We need a business card design for our personalize fashion service for our customers. the business card should reflect reliability, luxury and creativity.
The brand Gravetto is extracted from "Graceful Velvetto"; Gravetto provides fashion designs sprinkled with luxury and style tailored for our elite clients character profile.
Gravetto is created for those who embody class and elegance with a passion for style.
Target Market(s)
Affluent Customers
Industry/Entity Type
Fashion
Contact Information for Business Card
Samira Haddadin
Fashion Designer
Telephone: +971 4 555 0192
Mobile +971 50 555 0147
Emal info@gravetto-example.com
Website www.gravetto-example.com
Social Media Youtube g+ Facebook Instagram Pin /gravetto
Font styles to use
Other font styles liked:
- Audrey provided
Look and feel
Each slider illustrates characteristics of the customer's brand and the style your logo design should communicate.

```html
<!DOCTYPE html>
<html lang="en">
<head>
<meta charset="utf-8">
<title>Gravetto Business Card</title>
<link rel="stylesheet" href="https://fonts.googleapis.com/css2?family=Open+Sans:wght@300;400;600;700&display=swap">
<style>
  :root {
    --page-bg: #e6e6e6;
    --card-dark: #2e2d2e;
    --card-dark-ink: #1f1e1f;
    --card-light: #f4f4f4;
    --ink: #1c1c1c;
    --ink-soft: #333333;
    --rule: #2a2a2a;
  }
  * { box-sizing: border-box; margin: 0; padding: 0; }
  html, body {
    width: 1200px; height: 900px; overflow: hidden;
    background: var(--page-bg);
    font-family: "Open Sans", Arial, sans-serif;
    color: var(--ink);
  }
  .canvas {
    width: 1200px; height: 900px;
    display: flex; flex-direction: column; align-items: center; justify-content: center;
    gap: 40px;
  }
  .card {
    width: 700px; height: 400px;
    box-shadow: 0 6px 18px rgba(0,0,0,0.18);
    position: relative;
  }
  .card--back {
    background: var(--card-dark);
    display: flex; align-items: center; justify-content: center;
  }
  .back-mark {
    display: flex; flex-direction: column; align-items: center; gap: 18px;
  }
  .back-mark__square {
    width: 34px; height: 34px; border: 3px solid var(--card-dark-ink);
  }
  .back-mark__name {
    font-weight: 300; font-size: 26px; letter-spacing: 12px;
    color: var(--card-dark-ink); text-transform: uppercase; padding-left: 12px;
  }
  .card--front {
    background: var(--card-light);
    display: flex; align-items: center;
  }
  .brand {
    width: 335px;
    display: flex; flex-direction: column; align-items: center; gap: 26px;
  }
  .brand__square {
    width: 52px; height: 52px; border: 4px solid var(--ink-soft);
  }
  .brand__name {
    font-weight: 300; font-size: 30px; letter-spacing: 16px;
    text-transform: uppercase; color: var(--ink); padding-left: 16px;
  }
  .divider {
    width: 2px; height: 220px; background: var(--rule);
  }
  .details {
    padding-left: 40px;
    display: flex; flex-direction: column;
  }
  .details__name { font-weight: 700; font-size: 21px; line-height: 1.2; }
  .details__title { font-weight: 400; font-size: 16px; color: var(--ink-soft); margin-bottom: 16px; }
  .details__address { font-size: 16px; line-height: 1.35; margin-bottom: 14px; }
  .contact-list { list-style: none; font-size: 16px; line-height: 1.55; }
  .contact-list li { display: flex; align-items: center; gap: 10px; }
  .contact-list svg { width: 13px; height: 13px; flex: none; }
</style>
</head>
<body>
<main class="canvas">
  <section class="card card--back" aria-label="Card back">
    <div class="back-mark">
      <div class="back-mark__square"></div>
      <div class="back-mark__name">Gravetto</div>
    </div>
  </section>

  <section class="card card--front" aria-label="Card front">
    <div class="brand">
      <div class="brand__square"></div>
      <div class="brand__name">Gravetto</div>
    </div>
    <div class="divider"></div>
    <div class="details">
      <p class="details__name">Samira Haddadin</p>
      <p class="details__title">Fashion Designer</p>
      <p class="details__address">14 Marina Lane, Tower B<br>Dubai Design District, UAE.</p>
      <ul class="contact-list">
        <li>
          <svg viewBox="0 0 16 16" aria-hidden="true"><path d="M4 1l3 3-1.5 2a9 9 0 0 0 4.5 4.5L12 9l3 3-2 2.5C7 14 2 9 1.5 3z" fill="none" stroke="#1c1c1c" stroke-width="1.5"/></svg>
          +971 4 555 0192
        </li>
        <li>
          <svg viewBox="0 0 16 16" aria-hidden="true"><rect x="1" y="3" width="14" height="10" fill="#1c1c1c"/><path d="M1 3l7 6 7-6" fill="none" stroke="#f4f4f4" stroke-width="1.3"/></svg>
          info@gravetto-example.com
        </li>
        <li>
          <svg viewBox="0 0 16 16" aria-hidden="true"><circle cx="8" cy="8" r="6.5" fill="none" stroke="#1c1c1c" stroke-width="1.4"/><ellipse cx="8" cy="8" rx="3" ry="6.5" fill="none" stroke="#1c1c1c" stroke-width="1.2"/><path d="M1.5 8h13" stroke="#1c1c1c" stroke-width="1.2"/></svg>
          www.gravetto-example.com
        </li>
      </ul>
    </div>
  </section>
</main>
</body>
</html>
```